Professional Website for Leading Global Private Equity Real Estate Company

The company is a leading global Private Equity Real Estate (PERE). We need a homepage design, an inner page design, and color/font tweaks to the logo (color should be more soothing than current blue used in the logo). The logo website should project the company as global, professional, experienced, trustworthy, accessible, YOUNG, DYNAMIC, hi-tech. PLEASE SEE the attached Design Brief Word Doc for details.

Target Market(s)

institional investors and wealthy private individuals

Industry/Entity Type

Finance

Number of Pages Required

2 page

Font styles to use
Sans Serif
Other font styles liked:
• either like in https://www.ferndalequay.com/ or like in presentations (Montserrat Black & Montserrat Light, Century Gothic, Blair ITC, Almoni Neue DL 4.0 AAA Medium, Almoni DL AAA)

Requirements
Must have
• new color palette that is NOT based on current logo. they want a more soothing color palette than the blue in that logo. the new color palette should project: global, professional, experienced, trustworthy, accessible, YOUNG, DYNAMIC, hi-tech.
Nice to have
• the likes these sites: https://www.ferndalequay.com/ and https://www.tvr.law/

```html
<!DOCTYPE html>
<html lang="en">
<head>
<meta charset="utf-8">
<title>Corvana Real Estate</title>
<link rel="stylesheet" href="https://fonts.googleapis.com/css2?family=Montserrat:wght@300;400;500;600;700&family=Roboto:wght@400;500&display=swap">
<style>
:root{
  --teal:#1f6b5e;
  --teal-dark:#134e45;
  --teal-bright:#1a9a83;
  --ink:#2b2b2b;
  --text:#444;
  --muted:#666;
  --paper:#f2efed;
  --white:#fff;
  --line:#cfcfcf;
}
*{box-sizing:border-box;margin:0;padding:0}
html,body{width:1200px;height:3987px;overflow:hidden;background:#fff}
body{font-family:"Roboto",Arial,sans-serif;color:var(--text)}
.canvas{position:relative;width:1200px;height:3987px;overflow:hidden}
.abs{position:absolute}
.heading{font-family:"Montserrat",sans-serif;font-weight:500;color:var(--ink);letter-spacing:.5px}
.eyebrow{font-family:"Montserrat",sans-serif;font-weight:400;color:var(--teal-bright);font-size:15px;letter-spacing:1px}
.rule{position:absolute;height:3px;background:var(--ink)}
.btn{position:absolute;display:flex;align-items:center;justify-content:center;border-radius:30px;font-family:"Montserrat",sans-serif;font-weight:600;font-size:15px;letter-spacing:.5px}
.btn-solid{background:var(--teal);color:#fff}
.btn-outline{border:2px solid var(--teal);color:var(--teal);background:transparent}

.hero{left:0;top:0;width:1200px;height:706px;background:linear-gradient(160deg,#5d6a66 0%,#3d4a4a 40%,#6b5550 70%,#3b4446 100%)}
.topbar{left:0;top:0;width:1200px;height:78px;background:rgba(30,30,30,.55)}
.brand{left:100px;top:14px;display:flex;align-items:center;gap:12px;color:#fff;font-family:"Montserrat",sans-serif;font-weight:500;font-size:19px;line-height:1.15;letter-spacing:1px}
.brand-dot{width:50px;height:50px;border-radius:50%;background:#fff}
.nav a{position:absolute;top:34px;color:#fff;font-family:"Montserrat",sans-serif;font-size:13px;font-weight:500;text-decoration:none;letter-spacing:.3px}
.login{left:1000px;top:26px;width:117px;height:34px;border:2px solid #fff;border-radius:20px;color:#fff;font-family:"Montserrat",sans-serif;font-size:13px;display:flex;align-items:center;justify-content:center}
.hero-title{left:0;width:1200px;text-align:center;color:#fff;font-family:"Montserrat",sans-serif;font-size:48px;line-height:54px}

.stat-num{font-family:"Montserrat",sans-serif;font-weight:700;font-size:40px;color:var(--teal-bright)}
.stat-label{font-family:"Montserrat",sans-serif;font-size:15px;color:var(--ink);margin-top:4px}
.divider{position:absolute;width:1px;background:var(--line)}

.pattern{background:var(--paper)}
.card{position:absolute;top:1307px;width:212px;height:250px;color:#fff;font-family:"Montserrat",sans-serif;font-weight:700;font-size:12.5px;line-height:17px}
.card .cap{position:absolute;left:28px;bottom:22px}

.body-copy{font-size:14.5px;line-height:27px;color:var(--text);text-align:center}
.field{position:absolute;border:1px solid #bbb;background:#fff;border-radius:28px;font-family:"Montserrat",sans-serif;font-size:12px;color:#555;padding-left:22px;display:flex;align-items:center}
.cfield{position:absolute;background:#fff;font-family:"Montserrat",sans-serif;font-size:12px;color:#666;padding:16px 18px}

.foot-h{font-family:"Montserrat",sans-serif;font-weight:500;font-size:15px;color:var(--teal-dark)}
.foot-list{list-style:none;font-size:13px;line-height:27px;color:#333}
.foot-contact{font-size:13px;color:#1d2d5a;display:flex;align-items:flex-start;gap:14px}
.icon{width:26px;height:26px;border-radius:50%;background:var(--teal-dark);flex:none;display:flex;align-items:center;justify-content:center}
.social{width:26px;height:26px;border-radius:50%;display:inline-block;margin-right:8px}
.fine{font-size:12px;color:#555}
</style>
</head>
<body>
<div class="canvas">

  <div class="abs hero" role="img" aria-label="Aerial photo of a container port with rows of stacked shipping containers"></div>
  <div class="abs topbar"></div>
  <div class="abs brand"><span class="brand-dot"></span><span>CORVANA<br>REAL ESTATE</span></div>
  <nav class="nav">
    <a style="left:356px">ABOUT US ⌄</a>
    <a style="left:466px">OUR BUSINESSES ⌄</a>
    <a style="left:627px">INVESTORS LOBBY</a>
    <a style="left:793px">NEWS</a>
    <a style="left:880px">CONTACT US</a>
  </nav>
  <div class="abs login">LOG IN</div>

  <svg class="abs" style="left:583px;top:239px" width="54" height="54" viewBox="0 0 54 54"><circle cx="27" cy="27" r="25" fill="none" stroke="#fff" stroke-width="2"/><path d="M21 17 L37 27 L21 37 Z" fill="#fff"/></svg>
  <div class="abs hero-title" style="top:308px;font-weight:700">LEADING GLOBAL PRIVATE</div>
  <div class="abs hero-title" style="top:362px;font-weight:300">EQUITY REAL ESTATE</div>
  <div class="btn btn-solid" style="left:513px;top:433px;width:187px;height:50px;background:var(--teal-bright)">ABOUT US ›</div>
  <svg class="abs" style="left:589px;top:608px" width="24" height="36" viewBox="0 0 24 36"><path d="M12 2 V32 M2 22 L12 32 L22 22" fill="none" stroke="#fff" stroke-width="2"/></svg>

  <div class="abs eyebrow" style="left:134px;top:784px">WHO WE ARE</div>
  <div class="abs heading" style="left:131px;top:802px;font-size:34px;line-height:39px;font-weight:600">ABOUT CORVANA<br>REAL ESTATE</div>
  <div class="rule" style="left:134px;top:892px;width:58px"></div>
  <p class="abs" style="left:480px;top:796px;width:580px;font-size:16px;line-height:28px">Lorem ipsum dolor sit amet, consectetur adipiscing elit, sed do eiusmod tempor incididunt ut labore et dolore magna aliqua. Ut enim ad minim veniam, quis nostrud exercitation ullamco laboris nisi ut aliquip ex ea com-modo consequat. Duis aute irure dolor in reprehenderi</p>

  <div class="abs" style="left:143px;top:1000px"><div class="stat-num">$250</div><div class="stat-label">REAL ESTATE PROJECTS</div></div>
  <div class="divider" style="left:372px;top:1015px;height:60px"></div>
  <div class="abs" style="left:413px;top:1000px"><div class="stat-num">$25B</div><div class="stat-label">PRIVATE EQUITY</div></div>
  <div class="divider" style="left:612px;top:1015px;height:60px"></div>
  <div class="abs" style="left:657px;top:1000px"><div class="stat-num">$13B</div><div class="stat-label">FUND SOLUTIONS</div></div>
  <div class="divider" style="left:850px;top:1015px;height:60px"></div>
  <div class="abs" style="left:906px;top:1000px"><div class="stat-num">$120B</div><div class="stat-label">CREDIT &amp; INSURANCE</div></div>

  <div class="abs pattern" style="left:0;top:1142px;width:1200px;height:510px"></div>
  <div class="abs eyebrow" style="left:0;top:1208px;width:1200px;text-align:center">WHAT WE DO</div>
  <div class="abs heading" style="left:0;top:1226px;width:1200px;text-align:center;font-size:32px">OUR INVESTMENT PLATFORMS</div>
  <div class="rule" style="left:567px;top:1266px;width:50px"></div>

  <div class="card" style="left:71px;background:linear-gradient(160deg,#2f3e55,#5a5f6e)" role="img" aria-label="Hand touching a digital private equity chart"><div class="cap">SED UT PERSPICIATIS<br>UNDE OMNIS</div></div>
  <div class="card" style="left:282px;background:var(--teal)">
    <div style="position:absolute;left:25px;top:55px;width:170px">SED UT PERSPICIATIS<br>UNDE OMNIS</div>
    <div style="position:absolute;left:25px;top:103px;width:160px;font-weight:400;font-size:10px;line-height:15px;color:#d8ebe7">Lorem ipsum dolor sit amet, consectetur adipiscing elit, sed do eiusmod tempor incididunt ut labore et</div>
    <div style="position:absolute;left:25px;top:180px;width:108px;height:28px;border:1.5px solid #fff;border-radius:16px;font-size:9px;display:flex;align-items:center;justify-content:center">LEARN MORE</div>
  </div>
  <div class="card" style="left:493px;background:linear-gradient(180deg,#6f8aa3,#3d4f5f)" role="img" aria-label="Modern glass office building at dusk"><div class="cap" style="left:22px">VATEM QUIA VOLUPTAS<br>SIT ASPERNATUR</div></div>
  <div class="card" style="left:704px;background:linear-gradient(180deg,#4f83b8,#23405e)" role="img" aria-label="Businessman facing a connected city skyline"><div class="cap" style="left:30px">SED UT PERSPICIATIS<br>UNDE OMNIS</div></div>
  <div class="card" style="left:915px;width:215px;background:linear-gradient(180deg,#b5b9bb,#4c5254)" role="img" aria-label="City skyscrapers in soft light"><div class="cap" style="left:33px">NEMO ENIM IPSAM<br>VOLUPTATEM</div></div>

  <div class="abs heading" style="left:0;top:1733px;width:635px;text-align:center;font-size:34px">OUR EDGE</div>
  <p class="abs body-copy" style="left:92px;top:1804px;width:450px">Lorem ipsum dolor sit amet, consectetur adipiscing elit, sed do eiusmod tempor incididunt ut co laboris nisi ut aliquip ex ea com-modo consequat. Duis aute irure dolor in reprehende</p>
  <p class="abs body-copy" style="left:88px;top:1899px;width:460px">Aabor et dolore magna aliqua. Ut enim ad minim veniam, quis nostrud exercitation ullamco laboris nisi ut aliquip ex ea commodo consequat. Duis aute irure dolor in reprehenderitd exercitation</p>
  <div class="btn btn-solid" style="left:186px;top:2003px;width:254px;height:52px">INVESTOR INFORMATION</div>
  <div class="abs" style="left:604px;top:1650px;width:596px;height:472px;background:linear-gradient(200deg,#f2f2f2 0%,#8d99a0 45%,#3d464c 100%)" role="img" aria-label="Two glass skyscrapers viewed from below"></div>
  <div class="abs" style="left:604px;top:2122px;width:596px;height:50px;background:#000"></div>

  <div class="abs pattern" style="left:0;top:2172px;width:1200px;height:385px"></div>
  <div class="abs heading" style="left:0;top:2270px;width:1180px;text-align:center;font-size:34px">STAY UPDATED</div>
  <div class="abs" style="left:0;top:2328px;width:1180px;text-align:center;font-size:16.5px;color:#333">Get our latest insights, firm announcements and Charitable Foundation updates.</div>
  <div class="field" style="left:139px;top:2380px;width:333px;height:52px">NAME*</div>
  <div class="field" style="left:481px;top:2380px;width:333px;height:52px">EMAIL*</div>
  <div class="btn btn-solid" style="left:823px;top:2378px;width:169px;height:52px">SUBSCRIBE</div>

  <div class="abs" style="left:0;top:2557px;width:599px;height:525px;background:linear-gradient(150deg,#d9d6d0,#9a958d 50%,#5c5a57)" role="img" aria-label="Colleagues discussing work around a laptop in an office"></div>
  <div class="abs heading" style="left:600px;top:2655px;width:597px;text-align:center;font-size:32px">OUR RESPONSIBILITY</div>
  <div class="rule" style="left:870px;top:2706px;width:58px"></div>
  <p class="abs body-copy" style="left:685px;top:2730px;width:425px;font-size:14px;line-height:23px">Lorem ipsum dolor sit amet, consectetur adipiscing elit, sed do eiusmod tempor incididunt ut</p>
  <p class="abs body-copy" style="left:685px;top:2790px;width:425px;font-size:14px;line-height:23px">Aabor et dolore magna aliqua. Ut enim ad minim veniam, quis nostrud exercitation ullamco laboris nisi ut aliquip ex ea com-modo consequat. Duis aute irure dolor in reprehenderit exer-citationa aliquua. Ut enim ad minim veniam.</p>
  <div class="btn btn-outline" style="left:811px;top:2905px;width:176px;height:50px">LEARN MORE</div>

  <div class="abs" style="left:0;top:3082px;width:1200px;height:520px;background:linear-gradient(135deg,var(--teal-dark),var(--teal))"></div>
  <div class="abs" style="left:121px;top:3176px;color:#fff;font-family:Montserrat,sans-serif;font-size:14px;letter-spacing:1px">CONTACT US</div>
  <div class="abs" style="left:119px;top:3192px;color:#fff;font-family:Montserrat,sans-serif;font-weight:500;font-size:32px">GET IN TOUCH</div>
  <div class="abs" style="left:121px;top:3234px;width:78px;height:3px;background:#fff"></div>
  <div class="cfield" style="left:117px;top:3255px;width:242px;height:42px;padding-top:14px">First Name</div>
  <div class="cfield" style="left:367px;top:3255px;width:242px;height:42px;padding-top:14px">Last Name</div>
  <div class="cfield" style="left:117px;top:3302px;width:242px;height:42px;padding-top:14px">Phone Number</div>
  <div class="cfield" style="left:367px;top:3302px;width:242px;height:42px;padding-top:14px">Email address</div>
  <div class="cfield" style="left:117px;top:3352px;width:492px;height:77px;padding-top:10px">Message</div>
  <div class="btn" style="left:117px;top:3442px;width:187px;height:46px;border:2px solid #fff;color:#fff;font-size:13.5px">SUBMIT MESSAGE</div>
  <div class="abs" style="left:690px;top:3167px;width:360px;height:360px;border-radius:50%;background:radial-gradient(circle at 55% 45%,#e8e8e8,#9fa3a5 60%,#5d6264)" role="img" aria-label="Skyscrapers seen from below inside a circular frame"></div>

  <div class="abs foot-h" style="left:119px;top:3663px">IMPORTANT LINKS</div>
  <ul class="abs foot-list" style="left:124px;top:3698px">
    <li>About Us</li><li>Our Businesses</li><li>Investor Lobby</li><li>News</li><li>Contact Us</li>
  </ul>
  <div class="divider" style="left:302px;top:3665px;height:200px"></div>
  <div class="abs foot-h" style="left:350px;top:3663px">EXPLORE CORVANA REAL ESTATE</div>
  <ul class="abs foot-list" style="left:352px;top:3698px">
    <li>Private Equity</li><li>Real Estate</li><li>Credit</li><li>Strategic Partners</li><li>Tactical Opportunities</li><li>Infrastructure</li>
  </ul>
  <ul class="abs foot-list" style="left:555px;top:3698px">
    <li>Insurance Solutions</li><li>Life Sciences</li><li>Portfolio Operations</li><li>Technology and Innovations</li><li>Registered Products</li>
  </ul>
  <div class="divider" style="left:780px;top:3665px;height:200px"></div>
  <div class="abs foot-h" style="left:843px;top:3663px">CONTACT DETAILS</div>
  <div class="abs foot-contact" style="left:848px;top:3702px">
    <span class="icon"><svg width="12" height="14" viewBox="0 0 12 14"><path d="M6 0C3 0 1 2.2 1 5c0 3.5 5 9 5 9s5-5.5 5-9c0-2.8-2-5-5-5z" fill="#fff"/><circle cx="6" cy="5" r="2" fill="#134e45"/></svg></span>
    <span>48 Harbor Crest Rd Suite B<br>Palm Vale, FL 33999</span>
  </div>
  <div class="abs foot-contact" style="left:848px;top:3754px;align-items:center">
    <span class="icon"><svg width="13" height="13" viewBox="0 0 13 13"><path d="M3 1l2 3-1.3 1.3c.8 1.7 2.3 3.2 4 4L9 8l3 2-1 2C6 12 1 7 1 2z" fill="#fff"/></svg></span>
    <span>555-014-2270</span>
  </div>
  <div class="abs foot-contact" style="left:848px;top:3790px;align-items:center">
    <span class="icon"><svg width="13" height="10" viewBox="0 0 13 10"><rect x="0.5" y="0.5" width="12" height="9" fill="none" stroke="#fff"/><path d="M1 1l5.5 4.5L12 1" fill="none" stroke="#fff"/></svg></span>
    <span>info@corvanarealty.com</span>
  </div>
  <div class="abs" style="left:853px;top:3832px">
    <span class="social" style="background:var(--teal-dark)"></span><span class="social" style="background:#bfc9c7"></span><span class="social" style="background:#bfc9c7"></span><span class="social" style="background:#bfc9c7"></span>
  </div>

  <div class="abs" style="left:0;top:3912px;width:1200px;height:1px;background:#ccc"></div>
  <div class="abs fine" style="left:113px;top:3940px">Copyright © 2022 Corvana Realestate</div>
  <div class="abs fine" style="left:829px;top:3940px">Terms of Use &nbsp;|&nbsp; Sitemap &nbsp;|&nbsp; Privacy Policy</div>

</div>
</body>
</html>
```